Modern/Bold/Unique Prenatal Vitamin label redesign

We are in need of a design update for our Prenatal Vitamin label. We want to modernize our label and give it a fresh feel.
It should bring a feeling of fun, joy, and sophistication, but also be bold/edgy/unique and portray Trust and Authority. Our buyers are mainly mothers in the age range of 25-34 who are pregnant or breastfeeding.
I will attach our current label design, as well as some inspiration to go off of.
We like the idea of having a clean, easy to read label label with bold/vibrant colors and fonts. We like the idea of having some retro vibes in it as well
Please see the attached artwork for design inspiration (New Design Idea). We like the idea of having a pregnant mother image like the attachment on the label, with the rest of the label being white. Please come up with a unique drawing/image for the design. We cannot use a copied image or stock image.
We look forward to working with you!

```html
<!DOCTYPE html>
<html lang="en">
<head>
<meta charset="utf-8">
<title>Prenatal Label Range</title>
<link href="https://fonts.googleapis.com/css2?family=Alfa+Slab+One&family=Montserrat:wght@400;700&family=Saira+Semi+Condensed:wght@600&display=swap" rel="stylesheet">
<style>
  :root {
    --stage: #d6cfe0;
    --white: #ffffff;
    --splash-top: #e8488f;
    --splash-mid: #5fb6d8;
    --splash-low: #f3a53a;
  }
  html, body { margin: 0; padding: 0; }
  body {
    width: 1200px; height: 2209px; overflow: hidden;
    background: var(--stage);
    font-family: "Montserrat", sans-serif;
    position: relative;
  }
  .label {
    position: absolute; left: 40px; width: 1120px; height: 502px;
    background: var(--white); overflow: hidden;
  }
  .label--prenatal { top: 281px; --base: #f5b0d3; --ink: #b51c72; --band: #b51c72; --line: #e47ab6; --accent: #ffffff; }
  .label--thistle { top: 853px; --base: #a092c8; --ink: #5e4796; --band: #66489c; --line: #7c66b2; --accent: #a993d1; }
  .label--postnatal { top: 1425px; --base: #45c3ee; --ink: #1564b0; --band: #1564b0; --line: #2a8fd4; --accent: #45c3ee; }

  .label__shapes { position: absolute; inset: 0; }
  .base-fill { fill: var(--base); }
  .frame-line { fill: none; stroke: var(--line); stroke-width: 2.5; }
  .band-fill { fill: var(--band); }
  .box-line { fill: none; stroke: var(--ink); stroke-width: 2; }
  .icon { fill: none; stroke: var(--white); stroke-width: 2; }

  .artwork {
    position: absolute; left: 250px; top: 0; width: 210px; height: 502px;
    background: linear-gradient(180deg, var(--splash-top) 0%, var(--splash-mid) 55%, var(--splash-low) 100%);
  }

  .brand {
    position: absolute; left: 516px; top: 42px;
    display: flex; align-items: center; gap: 9px;
    color: var(--white); font-weight: 700; font-size: 19px;
  }
  .brand__dot { width: 24px; height: 24px; border-radius: 50%; border: 2px solid var(--white); box-sizing: border-box; }

  .title {
    position: absolute; left: 490px; top: 80px; margin: 0;
    font-family: "Alfa Slab One", serif; font-weight: 400;
    font-size: 47px; line-height: 46px; color: var(--ink);
    text-shadow: 2px 2px 0 var(--white);
  }
  .tagline {
    position: absolute; left: 490px; top: 178px; margin: 0;
    color: var(--white); font-size: 15px; line-height: 17px;
  }
  .tagline strong { font-weight: 700; }
  .tagline .for { font-weight: 400; }
  .tagline .who { font-weight: 700; color: var(--accent); display: block; }

  .formula {
    position: absolute; left: 497px; top: 247px; margin: 0;
    color: var(--white); font-weight: 700; font-size: 14.5px; line-height: 14px;
  }
  .count {
    position: absolute; left: 611px; top: 246px;
    color: var(--white); display: flex; flex-direction: column;
  }
  .count__row { display: flex; align-items: center; gap: 3px; }
  .count__num { font-family: "Alfa Slab One", serif; font-size: 29px; line-height: 28px; }
  .count__unit { font-family: "Alfa Slab One", serif; font-size: 11px; line-height: 10px; }
  .count__note { font-family: "Alfa Slab One", serif; font-size: 8.6px; line-height: 10px; }

  .claims {
    position: absolute; left: 604px; top: 300px; margin: 0; padding: 0; list-style: none;
    font-family: "Saira Semi Condensed", sans-serif; font-weight: 600;
    font-size: 12.5px; line-height: 11.5px; color: var(--ink);
  }
  .claims li { height: 34px; display: flex; align-items: center; }
</style>
</head>
<body>

<section class="label label--prenatal">
  <div class="artwork" role="img" aria-label="Colourful watercolour illustration of an expecting mother holding a heart"></div>
  <svg class="label__shapes" width="1120" height="502" viewBox="0 0 1120 502">
    <rect class="base-fill" x="460" y="0" width="660" height="502"/>
    <path class="frame-line" d="M472 14 H752 A18 18 0 0 0 770 32 V34 A16 16 0 0 0 786 50 V452 A16 16 0 0 0 770 468 A18 18 0 0 0 752 486 H472"/>
    <path class="band-fill" d="M460 174 H725 V235 H460 Z"/>
    <path class="box-line" d="M490 242 H777 V288 H490 Z M598 242 L608 265 L598 288"/>
    <g class="icon">
      <rect x="572" y="304" width="22" height="14" fill="#fff"/>
      <path d="M574 335 Q574 350 590 350 Q596 338 592 328 Q582 336 574 335"/>
      <circle cx="584" cy="376" r="11"/>
      <circle cx="584" cy="410" r="11"/><path d="M578 410 l4 4 l8 -8"/>
      <path d="M572 444 q6 -10 12 0 t12 0 M572 444 q6 10 12 0 t12 0"/>
    </g>
  </svg>
  <div class="brand"><span class="brand__dot"></span>Bloom Nest</div>
  <h2 class="title">Prenatal<br>Plus</h2>
  <p class="tagline">Once Daily<br><strong>Premium Multivitamin</strong> <span class="for">for</span><span class="who">Mama &amp; Baby</span></p>
  <p class="formula">ADVANCED<br>FORMULA</p>
  <div class="count"><div class="count__row"><span class="count__num">90</span><span class="count__unit">VEGGIE<br>CAPSULES</span></div><span class="count__note">DIETARY SUPLEMENT</span></div>
  <ul class="claims">
    <li>FORMULATED<br>IN THE USA</li><li>VEGAN</li><li>GLUTTEN &amp; MAJOR<br>ALLERGEN FREE</li><li>GMP QUALITY<br>ASSURED</li><li>NON-GMO</li>
  </ul>
</section>

<section class="label label--thistle">
  <div class="artwork" role="img" aria-label="Colourful watercolour illustration of an expecting mother holding a heart"></div>
  <svg class="label__shapes" width="1120" height="502" viewBox="0 0 1120 502">
    <rect class="base-fill" x="460" y="0" width="660" height="502"/>
    <path class="frame-line" d="M472 14 H752 A18 18 0 0 0 770 32 V34 A16 16 0 0 0 786 50 V452 A16 16 0 0 0 770 468 A18 18 0 0 0 752 486 H472"/>
    <path class="band-fill" d="M460 174 H725 V235 H460 Z"/>
    <path class="box-line" d="M490 242 H777 V288 H490 Z M598 242 L608 265 L598 288"/>
    <g class="icon">
      <rect x="572" y="304" width="22" height="14" fill="#fff"/>
      <path d="M574 335 Q574 350 590 350 Q596 338 592 328 Q582 336 574 335"/>
      <circle cx="584" cy="376" r="11"/>
      <circle cx="584" cy="410" r="11"/><path d="M578 410 l4 4 l8 -8"/>
      <path d="M572 444 q6 -10 12 0 t12 0 M572 444 q6 10 12 0 t12 0"/>
    </g>
  </svg>
  <div class="brand"><span class="brand__dot"></span>Bloom Nest</div>
  <h2 class="title">Blessed<br>Thistle</h2>
  <p class="tagline">Once Daily<br><strong>Premium Multivitamin</strong> <span class="for">for</span><span class="who">Mama &amp; Baby</span></p>
  <p class="formula">ADVANCED<br>FORMULA</p>
  <div class="count"><div class="count__row"><span class="count__num">90</span><span class="count__unit">VEGGIE<br>CAPSULES</span></div><span class="count__note">DIETARY SUPLEMENT</span></div>
  <ul class="claims">
    <li>FORMULATED<br>IN THE USA</li><li>VEGAN</li><li>GLUTTEN &amp; MAJOR<br>ALLERGEN FREE</li><li>GMP QUALITY<br>ASSURED</li><li>NON-GMO</li>
  </ul>
</section>

<section class="label label--postnatal">
  <div class="artwork" role="img" aria-label="Colourful watercolour illustration of an expecting mother holding a heart"></div>
  <svg class="label__shapes" width="1120" height="502" viewBox="0 0 1120 502">
    <rect class="base-fill" x="460" y="0" width="660" height="502"/>
    <path class="frame-line" d="M472 14 H752 A18 18 0 0 0 770 32 V34 A16 16 0 0 0 786 50 V452 A16 16 0 0 0 770 468 A18 18 0 0 0 752 486 H472"/>
    <path class="band-fill" d="M460 174 H725 V235 H460 Z"/>
    <path class="box-line" d="M490 242 H777 V288 H490 Z M598 242 L608 265 L598 288"/>
    <g class="icon">
      <rect x="572" y="304" width="22" height="14" fill="#fff"/>
      <path d="M574 335 Q574 350 590 350 Q596 338 592 328 Q582 336 574 335"/>
      <circle cx="584" cy="376" r="11"/>
      <circle cx="584" cy="410" r="11"/><path d="M578 410 l4 4 l8 -8"/>
      <path d="M572 444 q6 -10 12 0 t12 0 M572 444 q6 10 12 0 t12 0"/>
    </g>
  </svg>
  <div class="brand"><span class="brand__dot"></span>Bloom Nest</div>
  <h2 class="title">Postnatal<br>Plus</h2>
  <p class="tagline">Once Daily<br><strong>Premium Multivitamin</strong> <span class="for">for</span><span class="who">Mama &amp; Baby</span></p>
  <p class="formula">ADVANCED<br>FORMULA</p>
  <div class="count"><div class="count__row"><span class="count__num">90</span><span class="count__unit">VEGGIE<br>CAPSULES</span></div><span class="count__note">DIETARY SUPLEMENT</span></div>
  <ul class="claims">
    <li>FORMULATED<br>IN THE USA</li><li>VEGAN</li><li>GLUTTEN &amp; MAJOR<br>ALLERGEN FREE</li><li>GMP QUALITY<br>ASSURED</li><li>NON-GMO</li>
  </ul>
</section>

</body>
</html>
```